SaaS Early tech startup business card design

Unique design for experience ecommerce platform company. the business cards will be used by executive members. conformance with color code is required.

```html
<!DOCTYPE html>
<html lang="en">
<head>
<meta charset="utf-8">
<title>Velto business cards</title>
<link rel="stylesheet" href="https://fonts.googleapis.com/css2?family=Roboto:wght@400;500;700&family=Montserrat:wght@500&display=swap">
<style>
  :root {
    --backdrop: #6b6869;
    --card-navy: #1e2036;
    --card-white: #f3f4f5;
    --teal: #1fa89a;
    --teal-deep: #145a66;
    --ink: #2b2d33;
    --tagline-light: #e9ecef;
  }
  html, body {
    margin: 0;
    padding: 0;
    width: 1200px;
    height: 1200px;
    overflow: hidden;
    background: var(--backdrop);
  }
  .canvas {
    position: relative;
    width: 1200px;
    height: 1200px;
    background: var(--backdrop);
    font-family: "Roboto", sans-serif;
  }
  .card {
    position: absolute;
    width: 592px;
    height: 350px;
    border-radius: 26px;
    overflow: hidden;
    box-shadow: 0 18px 34px rgba(0,0,0,0.35);
  }
  .card--front {
    left: 300px;
    top: 198px;
    background: var(--card-navy);
  }
  .card--back {
    left: 292px;
    top: 637px;
    background: var(--card-white);
  }
  .brand-name {
    position: absolute;
    margin: 0;
    font-family: "Roboto", sans-serif;
    font-weight: 700;
    color: var(--teal);
    line-height: 1;
    letter-spacing: -1px;
  }
  .brand-tagline {
    position: absolute;
    margin: 0;
    font-family: "Montserrat", sans-serif;
    font-weight: 500;
    text-transform: uppercase;
    white-space: nowrap;
  }
  .card--front .brand-name {
    left: 0;
    width: 100%;
    text-align: center;
    top: 112px;
    font-size: 104px;
  }
  .card--front .brand-tagline {
    left: 0;
    width: 100%;
    text-align: center;
    top: 210px;
    font-size: 16px;
    letter-spacing: 6px;
    color: var(--tagline-light);
  }
  .card--back .brand-name {
    right: 32px;
    top: 34px;
    font-size: 90px;
  }
  .card--back .brand-tagline {
    right: 34px;
    top: 122px;
    font-size: 12.5px;
    letter-spacing: 4.5px;
    color: var(--teal);
  }
  .line-art {
    position: absolute;
  }
  .card--front .line-art {
    left: 473px;
    top: 218px;
    width: 115px;
    height: 123px;
    border-radius: 30px;
    background: radial-gradient(ellipse at center, rgba(31,168,154,0.35), rgba(31,120,150,0.08) 70%, transparent);
  }
  .card--back .line-art {
    left: 421px;
    top: 207px;
    width: 172px;
    height: 143px;
    border-radius: 40px 40px 0 0;
    background: radial-gradient(ellipse at center, rgba(31,168,154,0.22), rgba(60,110,150,0.08) 70%, transparent);
  }
  .edge-dot {
    position: absolute;
    left: -88px;
    top: 41px;
    width: 100px;
    height: 100px;
    border-radius: 50%;
    background: var(--teal);
  }
  .holder {
    position: absolute;
    left: 36px;
    top: 68px;
  }
  .holder-name {
    margin: 0;
    font-size: 24px;
    font-weight: 700;
    color: var(--teal-deep);
    letter-spacing: -0.5px;
    line-height: 1.1;
  }
  .holder-role {
    margin: 2px 0 0;
    font-size: 15.5px;
    font-weight: 400;
    color: var(--ink);
  }
  .address {
    position: absolute;
    left: 36px;
    top: 190px;
    margin: 0;
    font-style: normal;
    font-size: 15.5px;
    line-height: 22px;
    color: var(--ink);
  }
  .contacts {
    position: absolute;
    left: 36px;
    top: 248px;
    margin: 0;
    padding: 0;
    list-style: none;
    font-size: 15.5px;
    color: var(--ink);
  }
  .contacts li {
    display: flex;
    align-items: center;
    height: 22px;
  }
  .contacts svg {
    width: 14px;
    height: 14px;
    margin-left: 8px;
    margin-right: 9px;
    flex: none;
  }
</style>
</head>
<body>
<div class="canvas">

  <section class="card card--front">
    <p class="brand-name">velto</p>
    <p class="brand-tagline">Built around you</p>
    <div class="line-art" role="img" aria-label="Decorative interwoven teal line pattern"></div>
  </section>

  <section class="card card--back">
    <div class="edge-dot"></div>

    <div class="holder">
      <p class="holder-name">Marek D.</p>
      <p class="holder-role">CTO/Owner</p>
    </div>

    <p class="brand-name">velto</p>
    <p class="brand-tagline">Built around you</p>

    <address class="address">
      Lumen Tower, Dubai<br>
      Palm Tech District, UAE
    </address>

    <ul class="contacts">
      <li>
        <svg viewBox="0 0 16 16" aria-hidden="true"><path fill="var(--teal-deep)" d="M2 6c0-2 2-3 6-3s6 1 6 3l-3 1-1-2H6L5 7 2 6zm2 2h8l1 6H3l1-6zm4 1.5a2 2 0 1 0 0 4 2 2 0 0 0 0-4z"/></svg>
        (00) 0111 VELTO
      </li>
      <li>
        <svg viewBox="0 0 16 16" aria-hidden="true"><rect x="1" y="3" width="14" height="10" fill="var(--teal-deep)"/><path d="M1.5 3.5 8 9l6.5-5.5M1.5 12.5 6 7.5M14.5 12.5 10 7.5" stroke="#fff" stroke-width="1.2" fill="none"/></svg>
        info@velto.net
      </li>
      <li>
        <svg viewBox="0 0 16 16" aria-hidden="true"><circle cx="8" cy="8" r="6.5" fill="var(--teal)"/><path d="M1.5 8h13M8 1.5c-3 3-3 10 0 13M8 1.5c3 3 3 10 0 13M3 4.5h10M3 11.5h10" stroke="#fff" stroke-width="0.9" fill="none"/></svg>
        www.velto.net
      </li>
    </ul>

    <div class="line-art" role="img" aria-label="Faint decorative interwoven line pattern in blue and teal"></div>
  </section>

</div>
</body>
</html>
```